Business Card Design

We are a non profit organization that holds 10 days of races and car shows to raise money for autism. We stage the largest vintage race event in the country and the only one held on city streets.

We need business cards for myself and for 100 volunteers that stage the event. We like our cards to look exciting and to capture the essence of vintage racing.

Target Market(s)

sponsors and volunteers - most in the auto industry. This is not a TRELWAY crowd

Industry/Entity Type

Non Profit

Contact Information for Business Card

Marcus Hollenbeck
Executive Director
Ridgeway Classic Motor Rally Society
2740 Orchard Lane, Suite 318
Pittsburgh, PA 15907
hollenbeck@rcmrs-example.org
cell 555 013-7482
www.rcmrs-example.org

Font styles to use
Sans Serif

Colors
ec2027

Requirements
Must have
• our logo place a car image.Could place racing image on back of card along with website

Must include this statement small somewhere:
Benefitting the Hearthline Families Network and Brookmere Learning Center

```html
<!DOCTYPE html>
<html lang="en">
<head>
<meta charset="utf-8">
<title>Ridgeway Classic Motor Rally Society – Business Card</title>
<link rel="stylesheet" href="https://fonts.googleapis.com/css2?family=Montserrat:wght@400;500;600&display=swap">
<style>
  :root {
    --red: #ec2027;
    --red-deep: #c81a20;
    --charcoal: #3a3a3c;
    --ink: #333333;
    --muted: #6a6a6c;
    --paper: #ffffff;
    --backdrop: #e4e4e6;
  }
  * { margin: 0; padding: 0; box-sizing: border-box; }
  html, body { width: 1200px; height: 988px; overflow: hidden; }
  body {
    background: var(--backdrop);
    font-family: "Montserrat", sans-serif;
    position: relative;
  }
  .card {
    position: absolute;
    left: 220px;
    width: 760px;
    height: 434px;
    background: var(--paper);
    overflow: hidden;
    box-shadow: 0 6px 18px rgba(0,0,0,0.18);
  }
  .card--back { top: 40px; }
  .card--front { top: 514px; }

  /* back side */
  .stripe {
    position: absolute;
    left: 0; right: 0;
    background: var(--red);
    border-bottom: 4px solid var(--red-deep);
  }
  .stripe--upper { top: 34px; height: 96px; }
  .stripe--lower { top: 262px; height: 96px; }
  .racing-scene {
    position: absolute;
    left: 0; right: 0;
    top: 130px; height: 132px;
    background: linear-gradient(90deg, #d9d9db 0%, #8e8e92 50%, #d9d9db 100%);
  }

  /* front side */
  .header-band {
    position: absolute;
    left: 0; right: 0;
    top: 30px; height: 180px;
    background: var(--charcoal);
  }
  .emblem {
    position: absolute;
    left: 48px; top: 113px;
    width: 114px; height: 114px;
    border-radius: 50%;
    background: var(--paper);
    border: 5px solid var(--red);
    display: flex; align-items: center; justify-content: center;
  }
  .emblem__name {
    font-size: 15px;
    font-weight: 600;
    letter-spacing: 1px;
    color: var(--charcoal);
  }
  .benefit-note {
    position: absolute;
    left: 48px; top: 300px;
    width: 180px;
    font-size: 10px;
    line-height: 15px;
    font-weight: 400;
    color: var(--muted);
  }
  .identity {
    position: absolute;
    left: 250px; top: 232px;
  }
  .identity__name {
    font-size: 22px;
    font-weight: 500;
    letter-spacing: 2px;
    color: var(--red);
  }
  .identity__title {
    font-size: 14px;
    font-weight: 400;
    letter-spacing: 2px;
    color: var(--ink);
    margin-top: 4px;
  }
  .contacts {
    position: absolute;
    left: 250px; top: 300px;
    display: grid;
    grid-template-columns: 250px 240px;
    row-gap: 12px;
    column-gap: 14px;
  }
  .contact {
    display: flex; align-items: center; gap: 8px;
    font-size: 12px;
    color: var(--ink);
    white-space: nowrap;
  }
  .contact--wide { grid-column: 1 / 3; }
  .contact__icon { width: 16px; height: 16px; flex: none; }
  .rule {
    position: absolute;
    left: 0; right: 0;
    background: var(--red);
  }
  .rule--thick { top: 396px; height: 5px; }
  .rule--thin { top: 408px; height: 2px; }
</style>
</head>
<body>

<section class="card card--back" aria-label="Card back">
  <div class="stripe stripe--upper"></div>
  <div class="racing-scene" role="img" aria-label="Vintage race cars on a city street circuit"></div>
  <div class="stripe stripe--lower"></div>
</section>

<section class="card card--front" aria-label="Card front">
  <div class="header-band"></div>
  <div class="emblem"><span class="emblem__name">RIDGEWAY</span></div>

  <p class="benefit-note">Benefitting the Hearthline Families Network and Brookmere Learning Center</p>

  <div class="identity">
    <div class="identity__name">MARCUS HOLLENBECK</div>
    <div class="identity__title">EXECUTIVE DIRECTOR</div>
  </div>

  <div class="contacts">
    <div class="contact">
      <svg class="contact__icon" viewBox="0 0 16 16" aria-hidden="true"><circle cx="8" cy="8" r="8" fill="#ec2027"/><path d="M5.2 4.2l1.4-.2.8 2-1 .7a5 5 0 0 0 2.9 2.9l.7-1 2 .8-.2 1.4c-3.7.3-6.9-2.9-6.6-6.6z" fill="#fff"/></svg>
      <span>555 013-7482</span>
    </div>
    <div class="contact">
      <svg class="contact__icon" viewBox="0 0 16 16" aria-hidden="true"><circle cx="8" cy="8" r="8" fill="#ec2027"/><path d="M5.2 4.2l1.4-.2.8 2-1 .7a5 5 0 0 0 2.9 2.9l.7-1 2 .8-.2 1.4c-3.7.3-6.9-2.9-6.6-6.6z" fill="#fff"/></svg>
      <span>555 013-7482</span>
    </div>
    <div class="contact">
      <svg class="contact__icon" viewBox="0 0 16 16" aria-hidden="true"><circle cx="8" cy="8" r="8" fill="#ec2027"/><rect x="4" y="5" width="8" height="6" fill="none" stroke="#fff" stroke-width="1"/><path d="M4 5l4 3.2L12 5" fill="none" stroke="#fff" stroke-width="1"/></svg>
      <span>hollenbeck@rcmrs-example.org</span>
    </div>
    <div class="contact">
      <svg class="contact__icon" viewBox="0 0 16 16" aria-hidden="true"><circle cx="8" cy="8" r="8" fill="#ec2027"/><circle cx="8" cy="8" r="4" fill="none" stroke="#fff" stroke-width="1"/><path d="M4 8h8M8 4c-1.6 2.4-1.6 5.6 0 8M8 4c1.6 2.4 1.6 5.6 0 8" fill="none" stroke="#fff" stroke-width="0.9"/></svg>
      <span>www.rcmrs-example.org</span>
    </div>
    <div class="contact contact--wide">
      <svg class="contact__icon" viewBox="0 0 16 16" aria-hidden="true"><circle cx="8" cy="8" r="8" fill="#ec2027"/><path d="M8 12.5s-3-3.2-3-5.3a3 3 0 0 1 6 0c0 2.1-3 5.3-3 5.3z" fill="#fff"/><circle cx="8" cy="7.2" r="1.1" fill="#ec2027"/></svg>
      <span>2740 Orchard Lane, Suite 318</span>
    </div>
  </div>

  <div class="rule rule--thick"></div>
  <div class="rule rule--thin"></div>
</section>

</body>
</html>
```